"Vine Hollow Excursions" is a top notch Santa Barbara County Wine Tour company.

We provide scenic, boutique and custom wine tours. I need the card to be clean and classy. I will provide our logo. I would like the logo to cover the back side of the card as an option and would like to see a couple color options other then our signature green and gold. I would like to see some creative options and let the designers come up with options.
I need cards for myself and my team. The final design should communicate "An authentic and boutique wine tour experience"
Please use my website for reference www.vinehollowexcursions.example

Target Market(s)

We have a wide range of clients from millennials to baby boomers

Industry/Entity Type

Tour

Contact Information for Business Card

Contact info:
Dale Morton
805-219-6384
info@vinehollowexcursions.example
vinehollowexcursions.example

Colors

Designer to choose colors to be used in the design.

Requirements
Must have
• my logo
Nice to have
• *I would like to have the backside side with the logo and the company statement
• "An authentic and boutique wine tour experience" as an option.
• *I would also like to see what the designers can create!
• *I would like to see an option that incorporates or social: instagram, yelp, trip advisor
Should not have
• I do not want it too busy.

```html
<!DOCTYPE html>
<html lang="en">
<head>
<meta charset="utf-8">
<title>Vine Hollow Excursions – Business Card</title>
<link rel="stylesheet" href="https://fonts.googleapis.com/css2?family=Cormorant+Garamond:wght@400;500&family=Work+Sans:wght@400&display=swap">
<style>
  :root {
    --backdrop: #4b423a;
    --vine-green: #44684a;
    --paper: #ffffff;
    --gold: #a58b68;
    --sage-light: #dfe8df;
    --ink-light: #f4f6f2;
  }
  * { box-sizing: border-box; margin: 0; padding: 0; }
  html, body { width: 1200px; height: 930px; overflow: hidden; }
  body {
    background: var(--backdrop);
    position: relative;
    font-family: "Work Sans", sans-serif;
  }
  .card {
    position: absolute;
    width: 645px;
    height: 369px;
    overflow: hidden;
    box-shadow: 0 4px 10px rgba(0,0,0,0.35);
  }
  .card--front { left: 278px; top: 75px; background: var(--paper); }
  .card--back { left: 277px; top: 486px; background: var(--vine-green); }

  .scene-art {
    position: absolute; left: 0; top: 0; width: 645px; height: 250px;
    background: linear-gradient(180deg, var(--paper) 0%, var(--paper) 40%, var(--sage-light) 62%, var(--vine-green) 100%);
  }
  .green-band {
    position: absolute; left: 0; top: 250px; width: 645px; height: 119px;
    background: var(--vine-green);
  }
  .brand-name {
    font-family: "Cormorant Garamond", serif;
    font-weight: 500;
    text-transform: uppercase;
    letter-spacing: 0.06em;
  }
  .card--front .brand-name {
    position: absolute; right: 32px; top: 44px;
    font-size: 22px; color: var(--gold);
  }
  .person-name {
    position: absolute; right: 32px; top: 228px;
    font-family: "Cormorant Garamond", serif; font-weight: 400;
    font-size: 33px; color: var(--ink-light); letter-spacing: 0.01em;
    text-transform: uppercase; line-height: 1;
  }
  .rule {
    position: absolute; left: 33px; top: 272px; width: 507px; height: 2px;
    background: var(--ink-light);
  }
  .person-title {
    position: absolute; right: 32px; top: 262px;
    font-size: 16px; color: var(--ink-light);
  }
  .contact-list {
    position: absolute; left: 33px; top: 285px; list-style: none;
    color: var(--ink-light); font-size: 16px; line-height: 20px;
  }
  .contact-list li { display: flex; align-items: center; }
  .contact-list svg { width: 12px; height: 12px; margin-right: 13px; flex: none; }
  .address {
    position: absolute; right: 32px; top: 305px; text-align: right;
    color: var(--ink-light); font-size: 16px; line-height: 20px;
    font-style: normal;
  }
  .card--back .brand-name {
    position: absolute; left: 0; right: 0; top: 160px; text-align: center;
    font-size: 38px; color: var(--ink-light);
  }
</style>
</head>
<body>
  <section class="card card--front">
    <div class="scene-art" role="img" aria-label="Illustration of a rising sun with rays over green mountain ridges"></div>
    <div class="green-band"></div>
    <div class="brand-name">Vine Hollow Excursions</div>
    <div class="person-name">Dale Morton</div>
    <div class="rule"></div>
    <div class="person-title">Founder</div>
    <ul class="contact-list">
      <li>
        <svg viewBox="0 0 12 12" aria-hidden="true"><path d="M3 1 L4.6 3.4 L3.6 4.6 Q4.6 7 7.4 8.4 L8.6 7.4 L11 9 L10 11 Q4 11 1 2 Z" fill="none" stroke="currentColor" stroke-width="1.1"/></svg>
        805-219-6384
      </li>
      <li>
        <svg viewBox="0 0 12 12" aria-hidden="true"><rect x="1" y="2.5" width="10" height="7" fill="none" stroke="currentColor" stroke-width="1.1"/><path d="M1 3 L6 6.5 L11 3" fill="none" stroke="currentColor" stroke-width="1.1"/></svg>
        info@vinehollowexcursions.example
      </li>
      <li>
        <svg viewBox="0 0 12 12" aria-hidden="true"><circle cx="6" cy="6" r="5" fill="none" stroke="currentColor" stroke-width="1"/><ellipse cx="6" cy="6" rx="2.2" ry="5" fill="none" stroke="currentColor" stroke-width="1"/><path d="M1 6 H11 M2 3.5 H10 M2 8.5 H10" stroke="currentColor" stroke-width="0.8"/></svg>
        www.vinehollowexcursions.example
      </li>
    </ul>
    <address class="address">418 Larkspur Ln.<br>Solvang, CA 93463</address>
  </section>

  <section class="card card--back">
    <div class="brand-name">Vine Hollow Excursions</div>
  </section>
</body>
</html>
```